Upstart Retirement Planning Firm needs help with business card design

Harborview Nest Advisors, LLC is looking for help with business card design. We give advice on investments, insurance, and other financial matters related to retirement. There are some required disclosures that we will provide but mostly we are looking for a professional, classy business card that reflects the theme we have chosen. We have a logo that is attached but we would like to add a phrase; "Turning Your Earned Income Into Retirement Income"

Doubled sided only so that we can add the required disclosures (needed for our industry) on the back of the card. We will provide the exact words for this in 1-2 days.

Target Market(s)

Retirees and Pre-retirees. Professionals 50+ years old

Industry/Entity Type

Financial Planning

Contact Information for Business Card

We currently have two people who will need separate cards so we'd like to have a template so that we can add names for new cards in the future.

For the first run, please show the following information.

Gregor Pelham, MBA, ChFC®, CLU®
Financial Advisor, Registered Representative
gpelham@harborviewnest.example
Phone: (555) 318-2946
Toll Free Fax: (800) 555-0193

Address is
2187 Meadowlark Ridge Rd.
Suite K418
Virginia Beach, VA 23999

Colors
3277b5

Requirements
Must have
• Logo, contact info, small phase to describe business (in description), required legal disclosures on back of the card as follows (in small font)
• Gregor Pelham is a registered representative of and offers securities through Brightmoor Capital Brokerage Corporation, Member FNQX. Brightmoor Capital Brokerage Corporation is a member of the Brightmoor Capital Alliance which is the marketing name for Brightmoor Holding Corporation and its affiliates.
Nice to have
• Rounded edges, raised letters
Should not have
• any colors that aren't in the logo (other than black for font)

```html
<!DOCTYPE html>
<html lang="en">
<head>
<meta charset="utf-8">
<title>Harborview Nest Advisors – Business Card</title>
<link rel="stylesheet" href="https://fonts.googleapis.com/css2?family=Carlito&family=Arimo&display=swap">
<style>
  :root {
    --brand-blue: #2a5a9c;
    --brand-gray: #9a9a9a;
    --ink: #1a1a1a;
    --paper: #ffffff;
    --backdrop: #ececec;
  }
  * { margin: 0; padding: 0; box-sizing: border-box; }
  html, body { width: 1189px; height: 1200px; overflow: hidden; }
  body {
    background: var(--backdrop);
    font-family: "Carlito", "Calibri", sans-serif;
    color: var(--ink);
    position: relative;
  }
  .card {
    position: absolute;
    left: 137px;
    width: 916px;
    background: var(--paper);
    box-shadow: 0 4px 10px rgba(0,0,0,0.25);
    overflow: hidden;
  }
  .card--front { top: 45px; height: 524px; }
  .card--back { top: 624px; height: 522px; }

  .firm-name {
    position: absolute;
    color: var(--brand-blue);
    font-weight: 400;
    text-align: center;
    line-height: 1.1;
    letter-spacing: 0.5px;
  }
  .card--front .firm-name {
    left: 53px; width: 374px; top: 70px;
    font-size: 40px;
  }
  .card--back .firm-name {
    left: 0; width: 100%; top: 150px;
    font-size: 58px;
  }

  .tagline {
    position: absolute;
    left: 0; width: 100%; top: 310px;
    text-align: center;
    font-size: 24px;
    font-style: italic;
    color: var(--brand-gray);
  }

  .disclosure {
    position: absolute;
    left: 80px; right: 80px; bottom: 40px;
    text-align: center;
    font-size: 14px;
    line-height: 19px;
    color: var(--ink);
  }

  .divider {
    position: absolute;
    left: 466px; top: 41px;
    width: 2px; height: 386px;
    background: var(--brand-gray);
  }

  .address {
    position: absolute;
    right: 487px; top: 284px;
    text-align: right;
    font-size: 25px;
    line-height: 31px;
    font-style: normal;
  }

  .person { position: absolute; left: 508px; top: 62px; }
  .person__name {
    font-family: "Arimo", sans-serif;
    font-weight: 400;
    color: var(--brand-blue);
    font-size: 36px;
    line-height: 42px;
  }
  .person__role { font-size: 25px; line-height: 31px; }

  .contacts {
    position: absolute; left: 508px; top: 284px;
    list-style: none;
    font-size: 25px; line-height: 31px;
  }
  .contacts li { display: flex; align-items: center; gap: 8px; }
  .contacts .contacts__email { font-size: 22px; }
  .contacts svg { width: 21px; height: 21px; flex: none; }

  .wave { position: absolute; left: 0; top: 0; }

  .back-rule-top { position: absolute; top: 0; left: 0; width: 100%; height: 6px; background: var(--brand-blue); }
  .back-rule-bottom { position: absolute; bottom: 0; left: 0; width: 100%; height: 9px; background: var(--brand-gray); }
</style>
</head>
<body>

<section class="card card--front" aria-label="Business card front">
  <svg class="wave" width="916" height="524" viewBox="0 0 916 524" aria-hidden="true">
    <path d="M0,442 C220,500 360,530 470,512 C640,484 780,422 916,412 L916,524 L0,524 Z" fill="var(--brand-blue)"/>
    <path d="M0,420 C220,470 380,500 480,490 C650,472 780,400 916,388 L916,398 C780,412 650,482 480,500 C380,508 220,482 0,432 Z" fill="var(--brand-gray)"/>
  </svg>

  <div class="firm-name">Harborview Nest<br>Advisors, LLC</div>

  <div class="divider"></div>

  <address class="address">
    2187 Meadowlark Ridge Rd.<br>
    Suite K418<br>
    Virginia Beach, VA 23999
  </address>

  <div class="person">
    <h1 class="person__name">Gregor Pelham</h1>
    <p class="person__role">Financial Advisor</p>
    <p class="person__role">Registered Representative</p>
    <p class="person__role">MBA, ChFC®, CLU®</p>
  </div>

  <ul class="contacts">
    <li>
      <svg viewBox="0 0 20 20" aria-label="Phone"><rect width="20" height="20" fill="var(--brand-blue)"/><path d="M6 4 L8.5 4 L9.5 7 L8 8.3 C8.8 10.2 9.8 11.2 11.7 12 L13 10.5 L16 11.5 L16 14 C16 15 15 16 14 16 C9 15.5 4.5 11 4 6 C4 5 5 4 6 4 Z" fill="#fff"/></svg>
      (555) 318-2946
    </li>
    <li>
      <svg viewBox="0 0 20 20" aria-label="Fax"><rect width="20" height="20" fill="var(--brand-blue)"/><rect x="6" y="3.5" width="8" height="4" fill="#fff"/><rect x="3.5" y="8" width="13" height="6" fill="#fff"/><rect x="6" y="12" width="8" height="4.5" fill="#fff" stroke="var(--brand-blue)" stroke-width="1"/></svg>
      (800) 555-0193
    </li>
    <li class="contacts__email">
      <svg viewBox="0 0 20 20" aria-label="Email"><rect width="20" height="20" fill="var(--brand-blue)"/><rect x="3.5" y="5.5" width="13" height="9" fill="#fff"/><path d="M3.5 5.5 L10 11 L16.5 5.5" fill="none" stroke="var(--brand-blue)" stroke-width="1.3"/></svg>
      gpelham@harborviewnest.example
    </li>
  </ul>
</section>

<section class="card card--back" aria-label="Business card back">
  <div class="back-rule-top"></div>
  <div class="firm-name">Harborview Nest<br>Advisors, LLC</div>
  <p class="tagline">Turning Your Earned Income Into Retirement Income</p>
  <p class="disclosure">Gregor Pelham is a registered representative of and offers securities through Brightmoor Capital Brokerage Corporation, Member FNQX. Brightmoor Capital Brokerage Corporation is a member of the Brightmoor Capital Alliance which is the marketing name for Brightmoor Holding Corporation and its affiliates.</p>
  <div class="back-rule-bottom"></div>
</section>

</body>
</html>
```